Website for Excavator and Earthworks Company

We require a modern, sleek and practical website for our newly created earthworks/excavator business in Perth, Western Australia called Bluegum Ridge Earthworks.

The website should have a modern, cutting edge feel but only needs to be relatively simplistic in it's layout and eventual functionality.

Some pages it should have would be Home, About, Projects and Contact Us.

```html
<!DOCTYPE html>
<html lang="en">
<head>
<meta charset="utf-8">
<title>Bluegum Ridge Earthworks</title>
<link href="https://fonts.googleapis.com/css2?family=Krona+One&family=Barlow:wght@400;500;600;700&display=swap" rel="stylesheet">
<style>
:root{
  --lime:#cde30c;
  --lime-soft:#f6fad2;
  --ink:#0c0c0c;
  --grey-field:#f0f0f0;
  --text:#333;
  --white:#fff;
  --footer-word:#1f1f1f;
}
*{box-sizing:border-box;margin:0;padding:0}
html,body{width:1200px;height:3482px;overflow:hidden}
body{font-family:"Barlow",sans-serif;color:var(--text);background:var(--white);position:relative}
.heading{font-family:"Krona One",sans-serif;text-transform:uppercase;color:var(--ink);letter-spacing:1px}
.abs{position:absolute}
.btn{position:absolute;display:flex;align-items:center;justify-content:center;font-weight:600;font-size:15px;text-decoration:none}
.btn-lime{background:var(--lime);color:var(--ink)}
.btn-outline{border:2px solid var(--white);color:var(--white)}
.btn-dark-outline{border:2px solid var(--ink);color:var(--ink)}
.band-line{position:absolute;left:0;width:1200px;background:var(--lime)}

/* header */
.site-header{position:absolute;top:0;left:0;width:1200px;height:64px;background:var(--white)}
.brand{position:absolute;left:124px;top:19px;display:flex;align-items:center;gap:10px;font-family:"Krona One",sans-serif;font-size:14px;color:var(--ink);text-transform:uppercase}
.brand-square{width:26px;height:26px;background:var(--lime)}
.nav a{position:absolute;top:24px;font-size:13px;font-weight:500;color:var(--ink);text-decoration:none}

/* hero */
.hero{position:absolute;top:64px;left:0;width:1200px;height:511px;background:radial-gradient(ellipse at 75% 20%,#7a5a3a 0%,#3b3024 45%,#1a1612 100%)}
.eyebrow{position:absolute;top:104px;left:0;display:flex;align-items:center;gap:8px;font-size:13px;font-weight:700;color:var(--lime);letter-spacing:1px}
.eyebrow i{display:block;width:119px;height:3px;background:var(--lime)}
.hero h1{position:absolute;left:124px;top:139px;font-size:40px;line-height:44px;color:var(--white)}
.hero p{position:absolute;left:124px;top:287px;width:320px;font-size:14px;line-height:18px;font-weight:700;color:var(--white)}
.quote-card{position:absolute;left:731px;top:49px;width:343px;height:395px;background:var(--white);border-top:8px solid #ddd}
.quote-card h2{position:absolute;left:0;width:100%;text-align:center;top:22px;font-size:27px}
.field{position:absolute;background:var(--grey-field);font-size:10px;color:#444;padding:14px 14px}
.field svg{position:absolute;right:12px;top:14px}
.send{position:absolute;left:34px;top:314px;width:274px;height:38px;background:var(--ink);color:var(--white);font-weight:700;font-size:14px;display:flex;align-items:center;justify-content:center}

/* about */
.about-title{position:absolute;top:671px;left:0;width:1200px;text-align:center;font-size:37px;line-height:44px}
.about-copy{position:absolute;left:124px;top:809px;width:240px;font-size:11px;line-height:16.3px;color:#333}
.about-copy p+p{margin-top:16px}
.photo{position:absolute}
.vision{position:absolute;left:780px;top:801px;width:294px;height:134px;border:1px solid #e4e4e4;padding:20px 22px}
.vision h3{font-size:22px;margin-bottom:10px}
.vision p{font-size:10.5px;line-height:16px;color:#333}
.feature{position:absolute;top:955px;width:134px;height:126px;background:var(--lime-soft);display:flex;flex-direction:column;align-items:center;padding-top:18px;text-align:center;font-size:12px;font-weight:600;line-height:16px;color:var(--ink)}
.feature svg{margin-bottom:6px}

/* services */
.services{position:absolute;top:1176px;left:0;width:1200px;height:750px;background:radial-gradient(ellipse at 60% 30%,#3a362c 0%,#221f19 60%,#151310 100%)}
.services h2{position:absolute;top:91px;left:0;width:1200px;text-align:center;color:var(--white);font-size:37px;line-height:44px}
.services .lead{position:absolute;top:186px;left:330px;width:540px;text-align:center;font-size:11px;line-height:16px;font-weight:600;color:var(--white)}
.service{position:absolute;top:248px;width:300px}
.service .img{width:300px;height:319px}
.service .badge{position:absolute;left:120px;top:287px;width:60px;height:60px;border-radius:50%;background:var(--lime);border:3px solid var(--white);display:flex;align-items:center;justify-content:center}
.service h3{position:absolute;top:362px;width:100%;text-align:center;color:var(--white);font-size:16px}
.service .rule{position:absolute;top:399px;width:300px;height:4px;background:var(--lime)}

/* gallery */
.gallery-title{position:absolute;top:2013px;left:0;width:1200px;text-align:center;font-size:37px}
.gallery-lead{position:absolute;top:2071px;left:370px;width:460px;text-align:center;font-size:11px;line-height:16px;color:#333}
.tile{position:absolute;width:300px;border-radius:10px}
.cta-title{position:absolute;top:2752px;left:0;width:1200px;text-align:center;font-size:23px}
.cta-lead{position:absolute;top:2781px;left:0;width:1200px;text-align:center;font-size:10.5px;color:#333}

/* band */
.band{position:absolute;top:2946px;left:0;width:1200px;height:162px;background:linear-gradient(90deg,#141414 0%,#1f1e1a 60%,#28303a 100%)}
.band h2{position:absolute;left:124px;top:60px;font-size:22px;line-height:31px;color:var(--white)}
.support{position:absolute;left:736px;top:72px;display:flex;gap:12px;align-items:center;color:var(--white)}
.support .ring{width:32px;height:32px;border-radius:50%;border:2px solid var(--white);display:flex;align-items:center;justify-content:center}
.support small{display:block;font-size:11px;font-weight:700}
.support strong{display:block;font-size:15px}

/* footer */
.footer{position:absolute;top:3118px;left:0;width:1200px;height:364px;background:#000;overflow:hidden}
.footer-brand{position:absolute;left:124px;top:146px;display:flex;align-items:center;gap:10px;font-family:"Krona One",sans-serif;font-size:16px;line-height:22px;color:var(--white);text-transform:uppercase}
.footer-brand span{display:block}
.footer-brand .sq{width:40px;height:40px;background:var(--lime)}
.col-title{position:absolute;top:52px;font-size:13px;font-weight:700;color:var(--lime)}
.col-link{position:absolute;font-size:11px;color:var(--white);font-weight:500}
.divider{position:absolute;top:50px;width:1px;height:140px;background:#2a2a2a}
.contact-row{position:absolute;left:912px;display:flex;gap:11px;align-items:center;color:var(--white);font-size:10.5px;line-height:14px}
.contact-row .dot{width:27px;height:27px;border-radius:50%;background:var(--white);display:flex;align-items:center;justify-content:center;flex:none}
.footer-word{position:absolute;top:222px;left:0;width:1200px;text-align:center;font-family:"Krona One",sans-serif;font-size:74px;color:var(--footer-word);white-space:nowrap;text-transform:uppercase}
.copyright{position:absolute;top:328px;left:0;width:1200px;text-align:center;font-size:10px;color:var(--white)}
</style>
</head>
<body>

<header class="site-header">
  <div class="brand"><span class="brand-square"></span>Bluegum Ridge Earthworks</div>
  <nav class="nav">
    <a style="left:508px">Home</a>
    <a style="left:580px">About</a>
    <a style="left:653px">Projects</a>
    <a style="left:740px">Contact Us</a>
  </nav>
  <a class="btn btn-lime" style="left:925px;top:14px;width:149px;height:36px">Get A Free Quote</a>
</header>

<section class="hero" role="img" aria-label="Dusky earthworks site with excavators at sunset">
  <div class="eyebrow"><i></i>BLUEGUM RIDGE EARTHWORKS</div>
  <h1 class="heading">Moving Earth.<br>Building<br>Foundations.</h1>
  <p>Providing expert earthworks, excavation, and site preparation services with precision, safety, and efficiency.</p>
  <a class="btn btn-lime" style="left:124px;top:359px;width:149px;height:38px">Get A Free Quote</a>
  <a class="btn btn-outline" style="left:286px;top:359px;width:137px;height:38px">View Our Work</a>

  <form class="quote-card">
    <h2 class="heading">Get A Quote</h2>
    <div class="field" style="left:34px;top:69px;width:130px;height:37px">Name</div>
    <div class="field" style="left:178px;top:69px;width:130px;height:37px">Phone</div>
    <div class="field" style="left:34px;top:124px;width:274px;height:36px">Email</div>
    <div class="field" style="left:34px;top:176px;width:274px;height:37px">Select Services
      <svg width="12" height="8" viewBox="0 0 12 8"><path d="M1 1l5 5 5-5" fill="none" stroke="#111" stroke-width="2"/></svg></div>
    <div class="field" style="left:34px;top:233px;width:274px;height:61px;padding-top:10px">Your Project Details</div>
    <div class="send">Send Message</div>
  </form>
</section>
<div class="band-line" style="top:575px;height:9px"></div>

<section>
  <h2 class="heading about-title">Building Strong<br>Foundations</h2>
  <div class="about-copy">
    <p>Based in Perth, Western Australia, Bluegum Ridge Earthworks is a premier excavation and earthmoving company specializing in residential, commercial, and civil projects. Our team of experienced professionals is dedicated to delivering exceptional results with precision and efficiency.</p>
    <p>We utilize the latest equipment and techniques to ensure your project is completed on time, within budget, and to the highest standards of safety and quality.</p>
  </div>
  <a class="btn btn-dark-outline" style="left:124px;top:1031px;width:100px;height:38px;font-size:13px">About Info</a>
  <div class="photo" role="img" aria-label="Yellow excavator digging soil under a blue sky" style="left:442px;top:801px;width:281px;height:280px;background:linear-gradient(180deg,#3f8ee0 0%,#8cc0ee 55%,#7a5a3c 70%,#4a3626 100%)"></div>
  <div class="vision">
    <h3 class="heading">Vision</h3>
    <p>Our vision is to deliver reliable, high-quality earthworks solutions that build strong foundations and long-term partnerships through trust, safety, and excellence.</p>
  </div>
  <div class="feature" style="left:780px">
    <svg width="22" height="40" viewBox="0 0 22 40"><rect x="6" y="0" width="10" height="8" fill="#111"/><rect x="2" y="10" width="18" height="6" fill="#111"/><rect x="8" y="16" width="6" height="14" fill="#111"/><path d="M8 30h6l-3 8z" fill="#111"/></svg>
    Modern<br>Machinery &amp;<br>Equipment</div>
  <div class="feature" style="left:940px">
    <svg width="26" height="36" viewBox="0 0 26 36"><rect x="2" y="2" width="22" height="34" fill="#111"/><g fill="#f6fad2"><rect x="6" y="7" width="4" height="4"/><rect x="16" y="7" width="4" height="4"/><rect x="6" y="15" width="4" height="4"/><rect x="16" y="15" width="4" height="4"/><rect x="6" y="23" width="4" height="4"/><rect x="16" y="23" width="4" height="4"/><rect x="10" y="30" width="6" height="6"/></g></svg>
    Residential,<br>Commercial &amp;<br>Civil Projects</div>
</section>

<section class="services" role="img" aria-label="Darkened background of a dump truck on an earthworks site">
  <h2 class="heading">Our Earthworks<br>Services</h2>
  <p class="lead">We provide reliable earthworks and site preparation services, delivering precision, safety, and efficiency across residential, commercial, and civil projects.</p>

  <div class="service" style="left:124px">
    <div class="img" role="img" aria-label="Site team in hi-vis vests and hard hats reviewing a plan" style="background:linear-gradient(180deg,#d8dde0 0%,#b8c2bf 50%,#8c8a7a 100%)"></div>
    <div class="badge"><svg width="26" height="26" viewBox="0 0 26 26"><rect x="3" y="3" width="20" height="20" rx="3" fill="none" stroke="#111" stroke-width="3"/><circle cx="13" cy="13" r="4" fill="#111"/></svg></div>
    <h3 class="heading">Site Preparation</h3>
    <div class="rule"></div>
  </div>
  <div class="service" style="left:450px">
    <div class="img" role="img" aria-label="Close view of an excavator bucket against a cloudy sky" style="background:linear-gradient(180deg,#5c8fc6 0%,#c9d8e4 45%,#6a5840 80%,#3a2e22 100%)"></div>
    <div class="badge"><svg width="26" height="26" viewBox="0 0 26 26"><path d="M6 22V8l8-5 6 6-4 4-4-3v12z" fill="#111"/></svg></div>
    <h3 class="heading">Excavation</h3>
    <div class="rule"></div>
  </div>
  <div class="service" style="left:775px">
    <div class="img" role="img" aria-label="Yellow excavator moving soil under a blue sky" style="background:linear-gradient(180deg,#2f7fd8 0%,#8ec3ee 60%,#8a6a48 75%,#5a4230 100%)"></div>
    <div class="badge"><svg width="28" height="26" viewBox="0 0 28 26"><rect x="2" y="14" width="24" height="8" rx="3" fill="#111"/><rect x="8" y="6" width="10" height="8" fill="#111"/><circle cx="12" cy="3" r="3" fill="#111"/></svg></div>
    <h3 class="heading">Earthmoving</h3>
    <div class="rule"></div>
  </div>
</section>

<section>
  <h2 class="heading gallery-title">Our Work Gallery</h2>
  <p class="gallery-lead">View our work across residential, commercial, and civil projects, delivered with expertise and attention to detail.</p>

  <div class="tile" role="img" aria-label="Orange excavator on a dirt mound" style="left:124px;top:2129px;height:314px;background:linear-gradient(180deg,#c9d3db 0%,#9aa6ae 55%,#6b5440 80%,#4b3a2c 100%)"></div>
  <div class="tile" role="img" aria-label="Excavator bucket dropping soil with dust" style="left:450px;top:2129px;height:242px;background:linear-gradient(135deg,#e2c060 0%,#b58a40 45%,#6a5030 100%)"></div>
  <div class="tile" role="img" aria-label="Bulldozer and skid steer clearing flat ground" style="left:775px;top:2129px;height:314px;background:linear-gradient(180deg,#3a85d8 0%,#a9cde8 45%,#8a7860 65%,#5e4e3c 100%)"></div>
  <div class="tile" role="img" aria-label="Red excavator beside rock and hills" style="left:124px;top:2468px;height:241px;background:linear-gradient(180deg,#6a7a88 0%,#b6bec4 50%,#7a7a76 100%)"></div>
  <div class="tile" role="img" aria-label="Two yellow excavators working in a rock quarry" style="left:450px;top:2397px;height:312px;background:linear-gradient(160deg,#8a8c88 0%,#c2b060 45%,#6e6e6a 100%)"></div>
  <div class="tile" role="img" aria-label="Excavators levelling a building site at dusk" style="left:775px;top:2468px;height:241px;background:linear-gradient(180deg,#7ea6d0 0%,#c6d4e0 45%,#8a6e58 70%,#5c4636 100%)"></div>

  <div class="abs" role="img" aria-label="Yellow excavator standing at the edge of the section" style="left:970px;top:2712px;width:230px;height:234px;background:radial-gradient(ellipse at 65% 65%,rgba(236,190,28,.95) 0%,rgba(236,190,28,.55) 40%,rgba(255,255,255,0) 72%)"></div>
  <h2 class="heading cta-title">Let's Get Your Project Moving</h2>
  <p class="cta-lead">Expert earthworks services to get your project started the right way.</p>
  <a class="btn btn-lime" style="left:525px;top:2817px;width:149px;height:36px;font-size:14px">Get A Free Quote</a>
</section>

<section class="band">
  <h2 class="heading">Driving Progress Through<br>Dependable Machinery</h2>
  <div class="support">
    <div class="ring"><svg width="16" height="16" viewBox="0 0 24 24"><path d="M6.6 10.8a15 15 0 006.6 6.6l2.2-2.2a1 1 0 011-.25 11.4 11.4 0 003.6.57 1 1 0 011 1V20a1 1 0 01-1 1A17 17 0 013 4a1 1 0 011-1h3.5a1 1 0 011 1c0 1.25.2 2.45.57 3.57a1 1 0 01-.25 1z" fill="#fff"/></svg></div>
    <div><small>GET QUICK SUPPORT</small><strong>08 9000 4127</strong></div>
  </div>
  <a class="btn btn-lime" style="left:925px;top:68px;width:149px;height:37px;font-size:14px">Get A Free Quote</a>
</section>
<div class="band-line" style="top:3108px;height:10px"></div>

<footer class="footer">
  <div class="footer-brand"><span class="sq"></span><div><span>Bluegum Ridge</span><span>Earthworks</span></div></div>

  <div class="col-title" style="left:434px">QUICK LINKS</div>
  <div class="col-link" style="left:434px;top:94px">Home</div>
  <div class="col-link" style="left:434px;top:121px">About</div>
  <div class="col-link" style="left:434px;top:148px">Projects</div>
  <div class="col-link" style="left:434px;top:175px">Contact Us</div>
  <div class="divider" style="left:608px"></div>

  <div class="col-title" style="left:665px">OUR SERVICES</div>
  <div class="col-link" style="left:665px;top:94px">Site Preparation</div>
  <div class="col-link" style="left:665px;top:121px">Excavation</div>
  <div class="col-link" style="left:665px;top:148px">Earthmoving</div>
  <div class="divider" style="left:824px"></div>

  <div class="col-title" style="left:911px">CONTACT INFO</div>
  <div class="contact-row" style="top:88px"><span class="dot"><svg width="12" height="14" viewBox="0 0 12 16"><path d="M6 0a6 6 0 00-6 6c0 4.5 6 10 6 10s6-5.5 6-10a6 6 0 00-6-6zm0 8.5A2.5 2.5 0 116 3.5a2.5 2.5 0 010 5z" fill="#000"/></svg></span><div>Location<br>Perth, Western Australia</div></div>
  <div class="contact-row" style="top:134px"><span class="dot"><svg width="13" height="13" viewBox="0 0 24 24"><path d="M6.6 10.8a15 15 0 006.6 6.6l2.2-2.2a1 1 0 011-.25 11.4 11.4 0 003.6.57 1 1 0 011 1V20a1 1 0 01-1 1A17 17 0 013 4a1 1 0 011-1h3.5a1 1 0 011 1c0 1.25.2 2.45.57 3.57a1 1 0 01-.25 1z" fill="#000"/></svg></span><div>Phone<br>08 9000 4127</div></div>
  <div class="contact-row" style="top:180px"><span class="dot"><svg width="13" height="10" viewBox="0 0 16 12"><rect x="0" y="0" width="16" height="12" rx="1" fill="#000"/><path d="M1 1l7 6 7-6" fill="none" stroke="#fff" stroke-width="1.4"/></svg></span><div>Email<br>info@bluegumridge.com.au</div></div>

  <div class="footer-word">Bluegum Ridge</div>
  <p class="copyright">© 2026 Bluegum Ridge Earthworks. All rights reserved.</p>
</footer>

</body>
</html>
```